Help our Sugar Loom find our winning design! We're looking for a business card....

We’re a Sugar Loom in NY specializing in custom-made cakes and unique desserts.
Our cakes combine flavor and art, each designed to match customer’s special event and theme.
We’d like a unique business card with a clean design that will combine French chic and artistic look & feel.
We’d like to differentiate ourselves from standard bakeries, please don’t offer cupcake images :-)
Our logo is peach-pink and brown and we’d love to use these colors ( . Another color that can be added is gold - or feel free to suggest!

Target Market(s)

Women, ages 25-55

Industry/Entity Type

Boutique

Contact Information for Business Card

Text on card:
Logo
Sugar Loom by Dana Welch

www.sugarloomsweets.com
hello@sugarloom.com
(516) 555-0147
F – sugarloomnyc
IG - sugarloom_ny

Font styles to use
Sans Serif
Script

Requirements
Must have
• Logo
• Clean look
• French chic and artistic look & feel.
Nice to have
• Damask pattern
Should not have
• Cupcake images

```html
<!DOCTYPE html>
<html lang="en">
<head>
<meta charset="utf-8">
<title>Sugar Loom – Business Card</title>
<link href="https://fonts.googleapis.com/css2?family=Great+Vibes&family=Open+Sans:wght@400;600&display=swap" rel="stylesheet">
<style>
  :root {
    --backdrop: #e4e4e4;
    --blush: #dba9a3;
    --blush-deep: #c98f88;
    --gold: #b98d2e;
    --gold-light: #e8c766;
    --cocoa: #2b1f1f;
    --paper: #ffffff;
    --script: "Great Vibes", cursive;
    --sans: "Open Sans", Arial, sans-serif;
  }
  html, body {
    margin: 0;
    width: 1200px;
    height: 852px;
    overflow: hidden;
    background: var(--backdrop);
  }
  .canvas {
    position: relative;
    width: 1200px;
    height: 852px;
  }
  .card {
    position: absolute;
    width: 530px;
    height: 303px;
    border-radius: 22px;
    overflow: hidden;
    box-shadow: 0 6px 18px rgba(0,0,0,0.18);
  }
  .card-front {
    left: 50px;
    top: 275px;
    background: linear-gradient(120deg, var(--blush) 0%, #e6b8b2 50%, var(--blush) 100%);
  }
  .card-back {
    left: 620px;
    top: 275px;
    background: linear-gradient(160deg, #fdf4f3 0%, var(--paper) 45%);
  }
  .front-brand {
    position: absolute;
    inset: 0;
    display: flex;
    align-items: center;
    justify-content: center;
    font-family: var(--script);
    font-size: 64px;
    color: var(--gold);
  }
  .back-art {
    position: absolute;
    inset: 0;
  }
  .back-brand {
    position: absolute;
    left: 40px;
    top: 58px;
    font-family: var(--script);
    font-size: 46px;
    color: var(--cocoa);
  }
  .contact-list {
    position: absolute;
    left: 40px;
    top: 160px;
    margin: 0;
    padding: 0;
    list-style: none;
    font-family: var(--sans);
    font-size: 13px;
    color: var(--cocoa);
  }
  .contact-list li {
    display: flex;
    align-items: center;
    gap: 9px;
    height: 21px;
  }
  .contact-icon {
    width: 12px;
    height: 12px;
    fill: var(--cocoa);
    flex: none;
  }
  .social-mark {
    width: 10px;
    height: 10px;
    background: var(--cocoa);
    border-radius: 2px;
    flex: none;
  }
  .owner {
    position: absolute;
    right: 26px;
    top: 140px;
    text-align: center;
  }
  .owner-line {
    font-family: var(--sans);
    font-size: 13px;
    color: var(--cocoa);
  }
  .owner-name {
    font-family: var(--script);
    font-size: 30px;
    color: var(--cocoa);
    line-height: 1.1;
  }
</style>
</head>
<body>
<main class="canvas">

  <section class="card card-front" aria-label="Card front">
    <div class="front-brand">Sugar Loom</div>
  </section>

  <section class="card card-back" aria-label="Card back">
    <svg class="back-art" viewBox="0 0 530 303" aria-hidden="true">
      <defs>
        <linearGradient id="goldSweep" x1="0" y1="1" x2="1" y2="0">
          <stop offset="0" stop-color="#9c7320"/>
          <stop offset="0.45" stop-color="#e8c766"/>
          <stop offset="1" stop-color="#a87c25"/>
        </linearGradient>
      </defs>
      <path class="blush-field" d="M430 0 C360 70 330 200 140 303 L530 303 L530 0 Z" fill="#dba9a3"/>
      <path class="gold-sweep" d="M560 70 C470 110 430 220 150 303 L180 303 C420 235 470 125 560 80 Z" fill="url(#goldSweep)"/>
      <path class="gold-ribbon" d="M415 0 C345 80 320 215 120 303 L135 303 C335 215 360 85 425 0 Z" fill="url(#goldSweep)"/>
    </svg>

    <div class="back-brand">Sugar Loom</div>

    <ul class="contact-list">
      <li>
        <svg class="contact-icon" viewBox="0 0 12 12"><path d="M2 1h2.5l1 2.5-1.3 1a6 6 0 0 0 3.3 3.3l1-1.3L11 7.5V10a1 1 0 0 1-1 1A9 9 0 0 1 1 2a1 1 0 0 1 1-1z"/></svg>
        (516) 555-0147
      </li>
      <li>
        <svg class="contact-icon" viewBox="0 0 12 12"><path d="M0 2h12v8H0z M1 3v.4l5 3.2 5-3.2V3z" fill-rule="evenodd"/></svg>
        hello@sugarloom.com
      </li>
      <li>
        <svg class="contact-icon" viewBox="0 0 12 12"><circle cx="6" cy="6" r="5.5"/><path d="M0.5 6h11M6 .5c-2.5 3-2.5 8 0 11M6 .5c2.5 3 2.5 8 0 11" stroke="#fff" stroke-width="0.9" fill="none"/></svg>
        www.sugarloomsweets.com
      </li>
      <li>
        <span class="social-mark"></span>
        sugarloomnyc
      </li>
    </ul>

    <div class="owner">
      <div class="owner-line">Sugar Loom by</div>
      <div class="owner-name">Dana Welch</div>
    </div>
  </section>

</main>
</body>
</html>
```